Bright Wave Labs

We need a professional letter head format for our company. Now we have a logo but need to desing a new logo also. I have uploaded our old logo. Use the color in the logo and design a new one.

Dear Designers , Need to mention "BWL" and please dont use our old LOGO. we need a new catchy one.

```html
<!DOCTYPE html>
<html lang="en">
<head>
<meta charset="utf-8">
<title>Bright Wave Labs — Letterhead</title>
<link href="https://fonts.googleapis.com/css2?family=Source+Sans+3:wght@400;600;700&family=Arimo:wght@700&display=swap" rel="stylesheet">
<style>
  :root {
    --backdrop: #e9eaeb;
    --paper: #ffffff;
    --ink: #333338;
    --navy: #0f1e35;
    --green: #8dc03f;
    --silver: #b7b9bc;
    --sig-tone: #e4e6ea;
  }
  * { box-sizing: border-box; margin: 0; padding: 0; }
  html, body { width: 1200px; height: 1200px; overflow: hidden; background: var(--backdrop); }
  .letterhead {
    position: absolute; left: 192px; top: 24px;
    width: 816px; height: 1152px;
    background: var(--paper);
    font-family: "Source Sans 3", "Myriad Pro", sans-serif;
    color: var(--ink);
    overflow: hidden;
  }
  .brand {
    position: absolute; left: 64px; top: 96px;
    display: flex; align-items: center; gap: 8px;
  }
  .brand-dot { width: 20px; height: 20px; border-radius: 50%; background: var(--green); }
  .brand-name { font-size: 17px; font-weight: 700; color: var(--navy); letter-spacing: .2px; }
  .contact { position: absolute; left: 605px; top: 39px; font-size: 11.5px; line-height: 17px; color: var(--navy); }
  .contact-group { border-left: 1px solid var(--navy); padding-left: 5px; margin-bottom: 8px; }
  .contact-line { display: flex; align-items: center; gap: 5px; font-size: 12.5px; }
  .contact-icon { width: 10px; height: 10px; border-radius: 2px; background: var(--green); flex: none; }
  .greeting {
    position: absolute; left: 69px; top: 215px;
    font-family: "Arimo", Arial, sans-serif; font-weight: 700; font-size: 17.5px; color: var(--navy);
  }
  .body-copy { position: absolute; left: 69px; top: 259px; width: 684px; }
  .body-copy p { font-size: 17.2px; line-height: 21.4px; text-align: justify; margin-bottom: 21px; }
  .signature {
    position: absolute; left: 64px; top: 748px; width: 128px; height: 38px;
    background: var(--sig-tone); border-radius: 4px;
  }
  .sign-off { position: absolute; left: 69px; top: 790px; font-size: 16.5px; font-weight: 600; color: var(--ink); }
  .footer-band { position: absolute; left: 0; bottom: 0; width: 816px; height: 34px; background: var(--navy); }
  .footer-rule { position: absolute; left: 0; bottom: 34px; width: 816px; height: 6px; background: var(--green); }
  .footer-rule::after { content: ""; position: absolute; left: 0; bottom: -2px; width: 100%; height: 2px; background: var(--silver); }
  .footer-url {
    position: absolute; left: 444px; bottom: 9px;
    font-size: 12.5px; letter-spacing: 1.2px; color: #fff;
  }
</style>
</head>
<body>
  <main class="letterhead">
    <div class="brand">
      <span class="brand-dot"></span>
      <span class="brand-name">Bright Wave Labs</span>
    </div>

    <div class="contact">
      <div class="contact-group">
        <div>Po. box 201, Street Name,</div>
        <div>City Name, Zip Code - 00000</div>
      </div>
      <div class="contact-group">
        <div class="contact-line"><span class="contact-icon"></span>(+925)555-014-207</div>
        <div class="contact-line"><span class="contact-icon"></span>info@brightwavelabs.com</div>
      </div>
    </div>

    <h1 class="greeting">Dear Mr. Adams,</h1>

    <section class="body-copy">
      <p>Lorem Ipsum is simply dummy text of the printing and typesetting industry. Lorem Ipsum has been the industry's standard dummy text ever since the 1500s, when an unknown printer took a galley of type and scrambled it to make a type specimen book. It has survived not only five centuries, but also the leap into electronic typesetting, remaining essentially unchanged.</p>
      <p>The standard chunk of Lorem Ipsum used since the 1500s is reproduced below for those interested. Sections 1.10.32 and 1.10.33 from "de Rebus Variis et Novis" by Marcus Vale are also reproduced in their exact original form, accompanied by English versions from the 1914 translation by H. Renwick</p>
      <p>Lorem Ipsum is simply dummy text of the printing and typesetting industry. Lorem Ipsum has been the industry's standard dummy text ever since the 1500s, when an unknown printer took a galley of type and scrambled it to make a type specimen book. It has survived not only five centuries, but also the leap into electronic typesetting, remaining essentially unchanged. It was popularised in the</p>
      <p>The standard chunk of Lorem Ipsum used since the 1500s is reproduced below for those interested. Sections 1.10.32 and 1.10.33 from "de Rebus Variis et Novis" by Marcus Vale are also reproduced in their exact original form, accompanied by English versions from the 1914 translation by H. Renwick</p>
    </section>

    <div class="signature" role="img" aria-label="Handwritten signature of the sender"></div>
    <div class="sign-off">Valued customers,</div>

    <div class="footer-rule"></div>
    <div class="footer-band"></div>
    <div class="footer-url">www.brightwavelabs.com</div>
  </main>
</body>
</html>
```